New Website Design for PHOVAN.org

We are looking for a new website design for PHOVAN.org. PHOVAN is a non profit home inspector association based in California. Home Inspectors are people that come out and look at a house before it's purchased to let the buyer know of any defects that may exist.
Our site is based on Joomla so if you'll be able to make a Joomla 3 template as well, please let us know (not required, but a bonus).
We would like to see designs that incorporate royal blue, white and chrome into the site as that's our main business colors.
We would like a place for rotating banners though they don't need to be the same size as the current site.
We would like navigation to be easier to manage with menus only across the top (via drop down menus) where we are going to sort out the items currently on the side. Possibly the front page could have a graphic link to separate portals for Realtors, Home Buyers and Inspectors, but that's just one option.
We would like a good mobile design or something that will scale easily to mobile.
The Find an Inspector feature is important and should stand out. The ASK PHOVANr site
Current home page feels a bit busy. Would like to simplify a bit.

```html
<!DOCTYPE html>
<html lang="en">
<head>
<meta charset="utf-8">
<title>PHOVAN – Home</title>
<link href="https://fonts.googleapis.com/css2?family=Lato:wght@400;700&family=Open+Sans:wght@400;600;700&family=PT+Sans:wght@400;700&display=swap" rel="stylesheet">
<style>
:root{
  --royal:#2e2a7a;
  --royal-bright:#2a2ad0;
  --text:#333;
  --muted:#8a8a8a;
  --line:#dcdcdc;
  --panel:#ececec;
  --card:#f7f7f7;
  --footer:#262626;
  --footer-bottom:#2d2d2d;
  --footer-text:#a8a8a8;
}
*{box-sizing:border-box;margin:0;padding:0}
html,body{width:866px;height:1200px;overflow:hidden;background:#fff}
body{position:relative;font-family:"Open Sans",sans-serif;color:var(--text)}
.abs{position:absolute}

.brand{left:80px;top:18px;display:flex;align-items:center;gap:10px}
.brand-mark{width:56px;height:56px;border-radius:50%;background:#e6e6ee;border:2px solid #c8c8d4}
.brand-name{font-family:"Lato",sans-serif;font-weight:700;color:var(--royal-bright);font-size:19px;line-height:21px}

.search{top:46px;height:20px;border:1px solid #cfcfcf;box-shadow:inset 0 1px 2px rgba(0,0,0,.12);font-size:7.5px;font-style:italic;color:#666;padding:6px 7px}
.search-btn{left:684px;top:46px;width:94px;height:20px;background:var(--royal);color:#fff;font-size:8px;font-weight:600;display:flex;align-items:center;justify-content:center;border-radius:2px}

.nav{left:79px;top:100px;width:709px;height:30px;border:1px solid var(--line);border-bottom:3px solid var(--line);display:flex;background:#fafafa}
.nav a{font-family:"Lato",sans-serif;font-size:10px;color:#333;text-decoration:none;display:flex;align-items:center;justify-content:center;border-right:1px solid var(--line)}
.nav a.active{background:#fff;color:var(--royal);border-top:2px solid var(--royal);margin-top:-1px}

.banner{left:79px;top:152px;width:709px;height:264px;background:linear-gradient(90deg,#e7e9ee 0%,#c9d0da 45%,#6d8fb8 70%,#9db6d1 100%);border-top:4px solid #ddd;border-bottom:3px solid #ddd}
.banner-title{left:93px;top:232px;font-family:"PT Sans",sans-serif;font-size:17px;line-height:25px;color:#222;letter-spacing:.2px}
.banner-btn{left:94px;top:315px;width:68px;height:22px;background:var(--royal);color:#fff;font-family:"PT Sans",sans-serif;font-weight:700;font-size:8.5px;display:flex;align-items:center;justify-content:center;border-radius:3px}
.dots{left:99px;top:396px;display:flex;gap:3px}
.dots i{width:5px;height:5px;border-radius:50%;background:#9a9a9a}
.dots i:first-child{background:#1f3a8a}

.welcome{left:0;width:866px;top:432px;text-align:center;font-family:"Lato",sans-serif;font-size:18px;color:var(--royal)}
.welcome b{color:#333;font-weight:700}
.intro{left:84px;width:698px;top:467px;text-align:center;font-family:Arial,sans-serif;font-size:11px;line-height:14px;color:#8a8a8a}
.section-title{left:93px;top:512px;font-family:"Lato",sans-serif;font-size:14px;color:#333}

.card{top:543px;width:217px;height:191px;background:var(--card);border-bottom:1px solid #e3e3e3}
.card-img{width:217px;height:108px}
.card h3{font-family:"Lato",sans-serif;font-weight:400;font-size:11.5px;letter-spacing:.3px;text-align:center;margin-top:16px;color:#333}
.card p{font-family:Arial,sans-serif;font-size:8.6px;line-height:11px;color:#999;padding:7px 15px 0}

.box{top:769px;height:191px;border:6px solid var(--panel);background:#fff;padding:8px 14px}
.box h4{font-family:"Open Sans",sans-serif;font-weight:700;font-size:10.5px;color:#222;margin-bottom:6px}
.links li{list-style:none;font-size:8.8px;color:#333;padding:6px 2px;border-bottom:1px solid #e6e6e6}
.view-all{display:inline-block;margin:4px 0 0 4px;font-size:10.5px;color:var(--royal);text-decoration:underline}
.event{font-size:8px;line-height:13px;color:#555;text-align:justify;padding:4px 0 7px;border-bottom:1px solid #e6e6e6;margin-bottom:3px}
.event:last-child{border:none}
.event a{color:var(--royal);font-weight:700;text-decoration:underline}
.login p{font-size:8px;color:#555;margin-bottom:12px}
.login label{display:block;font-size:8.6px;color:#333;margin-bottom:3px}
.login .field{height:19px;border:1px solid #cfcfcf;box-shadow:inset 0 1px 2px rgba(0,0,0,.1);margin-bottom:9px}
.login-btn{width:53px;height:20px;background:var(--royal);color:#fff;font-size:8px;font-weight:600;display:flex;align-items:center;justify-content:center;margin-top:2px}
.forgot{position:absolute;right:4px;bottom:4px;font-size:8px;font-weight:700;color:var(--royal);text-decoration:underline}

.footer{left:0;top:993px;width:866px;height:165px;background:var(--footer)}
.footer-bottom{left:0;top:1158px;width:866px;height:42px;background:var(--footer-bottom);border-top:1px solid #3a3a3a;color:#8c8c8c;font-size:7.5px;text-align:center;padding-top:17px}
.fcol{top:1015px;color:var(--footer-text);font-size:8.6px;line-height:13px}
.fcol h5{font-family:"Open Sans",sans-serif;font-weight:400;font-size:12px;color:#eee;margin-bottom:12px}
</style>
</head>
<body>

<header>
  <div class="abs brand">
    <span class="brand-mark"></span>
    <span class="brand-name">Pacific Home Valuation<br>Network · PHOVAN</span>
  </div>
  <div class="abs search" style="left:418px;width:117px">Distance..</div>
  <div class="abs search" style="left:544px;width:132px">Enter a zip or country</div>
  <div class="search-btn abs">Search for Inspector</div>
</header>

<nav class="abs nav">
  <a class="active" style="width:79px">Home</a>
  <a style="width:104px">Find an Inspector</a>
  <a style="width:142px">Home Buyers &amp; Sellers</a>
  <a style="width:119px">Real Estate Agents</a>
  <a style="width:87px">Inspectors</a>
  <a style="width:80px">Ask PHOVAN</a>
  <a style="width:98px;border-right:none">Conferences</a>
</nav>

<section>
  <div class="abs banner" role="img" aria-label="Photo of two inspectors in hard hats and safety vests looking up at a building"></div>
  <h1 class="abs banner-title" style="font-weight:400">THE SYMBOL OF REAL ESTATE<br>INSPECTION PROFESSIONALISM<br>IN STATE OF CALIFORNIA</h1>
  <div class="abs banner-btn">READ MORE</div>
  <div class="abs dots"><i></i><i></i><i></i><i></i><i></i></div>
</section>

<h2 class="abs welcome" style="font-weight:400">Welcome to a <b>PHOVAN</b></h2>
<p class="abs intro">Lorem Ipsum is simply dummy text of the printing and typesetting industry. Lorem Ipsum has been the industry's standard dummy text ever since the 1500s, when an unknown printer took a galley of type and scrambled it to make a type specimen book.</p>
<h3 class="abs section-title" style="font-weight:400">What We Do</h3>

<article class="abs card" style="left:93px">
  <div class="card-img" role="img" aria-label="Photo of an inspector in a hard hat taking notes" style="background:linear-gradient(135deg,#9fb8cf,#8a7a5e)"></div>
  <h3>PATH TO SUCCESS</h3>
  <p>Lorem Ipsum is simply dummy text of the printing and typesetting industry. Lorem Ipsum has been the industry's standard dummy text</p>
</article>
<article class="abs card" style="left:324px">
  <div class="card-img" role="img" aria-label="Photo of an open book in front of stacked books" style="background:linear-gradient(135deg,#6b4a2a,#c9a56e)"></div>
  <h3>EDUCATIONAL PUBLICATIONS</h3>
  <p>Lorem Ipsum is simply dummy text of the printing and typesetting industry. Lorem Ipsum has been the industry's standard dummy text</p>
</article>
<article class="abs card" style="left:555px">
  <div class="card-img" role="img" aria-label="Illustration of a figure leaning on a large red question mark" style="background:radial-gradient(circle at 50% 50%,#e8c4c4,#fff 70%);border:1px solid #ccc"></div>
  <h3>ASK PHOVAN</h3>
  <p>Lorem Ipsum is simply dummy text of the printing and typesetting industry. Lorem Ipsum has been the industry's standard dummy text</p>
</article>

<aside class="abs box" style="left:93px;width:216px">
  <h4>Home Inspection Software</h4>
  <ul class="links">
    <li>California Real Estate Inspection Law</li>
    <li>PHOVAN Chapter Meeting Locations</li>
    <li>Standards of Practice</li>
    <li>Code of Ethics</li>
    <li>Education / CEC's</li>
  </ul>
  <a class="view-all">View All</a>
</aside>

<aside class="abs box" style="left:329px;width:215px">
  <h4>Upcoming Events</h4>
  <p class="event">Lorem ipsum dolor sit amet, consectetuer adipiscing elit, sed diam nonummy nibh euismod tincidunt ut. <a>09-08-2013</a></p>
  <p class="event">Lorem ipsum dolor sit amet, consectetuer adipiscing elit, sed diam nonummy nibh euismod tincidunt. <a>09-08-2013</a></p>
  <p class="event">Lorem ipsum dolor sit amet, consectetuer adipiscing elit, sed diam nonummy nibh euismod tincidunt. <a>09-08-2013</a></p>
</aside>

<aside class="abs box login" style="left:565px;width:208px">
  <h4>Inspector Login</h4>
  <p>Lorem ipsum dolor sit amet, consectetuer</p>
  <label>Username</label><div class="field"></div>
  <label>Password</label><div class="field"></div>
  <div class="login-btn">LOGIN</div>
  <a class="forgot">Forgot Login?</a>
</aside>

<footer>
  <div class="abs footer"></div>
  <div class="abs fcol" style="left:106px">
    <h5>Popular</h5>
    Inspection FAQs<br>Common Venting of Gas<br>Becoming a Member<br>Education / CECs<br>Affiliate Directory
  </div>
  <div class="abs fcol" style="left:261px;width:195px">
    <h5>Business method</h5>
    Ma quande lingues coalesce, li grammatica del resultant lingue es plu simplic e regulari quam ti del coalescent lingues. Li nov lingua franca va esser plu simplic e regulari quam li existent Europan lingues.
  </div>
  <div class="abs fcol" style="left:502px;width:130px">
    <h5>Get in touch</h5>
    2400 Harbor Lane Suite 110<br>Riverton CA 95000-0000<br>Hours: M-F, 8:00am - 5:00pm<br>Phone: (800) 555-0142 or<br>(555) 010-2277<br>Fax: (555) 010-6719<br>Webmaster@PHOVAN.ORG
  </div>
  <div class="abs fcol" style="left:664px;width:100px">
    <h5>Who We are</h5>
    Established in 1976, PHOVAN is a non-profit trade association, with chapters located throughout the state. PHOVAN is a member-driven,
  </div>
  <div class="abs footer-bottom">Copyright © 2013 PHOVAN. All rights reserved.</div>
</footer>

</body>
</html>
```